Bright Trails, Strong Spirits Poster for American Indian Older Adults

We need am 11" x 17" poster designed for a health outreach project designed to reach older U.S. American Indians. The materials developed through this project will be distributed to American Indian and Alaska Native tribes, communities and tribal-serving organizations across the U.S. (more than 500 different tribes). If we find a successful design we will work with that designer to produce at least one other item we need design work for using the same look/feel and maybe other materials for this project. (more work!). The poster will include a set of facts (bulleted list on the attached document) that we would like presented in an "infographic" style. The design must be reflective of the American Indian culture and designed with older adults (65 and older) in mind. Imagery plays a strong role in the American Indian culture in the U.S. images of the heart, water, feathers, circle of life, etc. If you use photos of people they must include older adults and they must be American Indian (Native American). We prefer deep earth tones for the color scheme. The design must take into account design principles for older adults: 1. Try not to put colored font on colored background 2. Ensure high contrast for text 3. Font style should be sans serif, not cursive,decorative or heavily stylized because it is harder to read 4. Avoid using all caps 5. Don't print sideways or on top of images, shaded, backgrounds, etc. 6. All images should related specifically to the content of the text and be culturally appropriate for both older adults and American Indians. The final design should be easy to read and appeal to older American Indian adults. We need to incorporate three logos on the poster towards the bottom they should not be the center/focus of the poster. We also need to include a statement about who produced the materials- that can be very small below the logos at the bottom of the poster. We've attached the text for the poster and three logo files (note one is solid blue- we will finalize that after the document design is selected but need a placeholder for that logo.

Target Market(s)

Older adult (65 and older) American Indian and Alaska Natives and their family members in tribes, communities and tribal-serving organizations across the US

Font styles to use
Sans Serif

Requirements
Must have
• Must adhere to good design principles for older adults (listed in project description)
• Must feature culturally appropriate/targeted imagery and design look and feel

```html
<!DOCTYPE html>
<html lang="en">
<head>
<meta charset="utf-8">
<title>Bright Trails, Strong Spirits</title>
<link rel="stylesheet" href="https://fonts.googleapis.com/css2?family=Montserrat:ital,wght@0,500;0,600;0,700;0,800;1,600;1,700&display=swap">
<style>
  :root {
    --cream: #f6eedd;
    --cream-deep: #ecdfc2;
    --band-dark: #5e3d22;
    --band-light: #a37848;
    --brown: #6b4320;
    --brown-dark: #5a3818;
    --ink: #231f1c;
    --ink-soft: #3a332d;
    --white: #ffffff;
    --sage: #8fa595;
    --photo-light: #e9e2d4;
    --photo-mid: #cfc6b4;
    --logo-red: #c2412d;
    --logo-green: #3f8a3c;
  }
  * { box-sizing: border-box; margin: 0; padding: 0; }
  html, body { width: 775px; height: 1200px; overflow: hidden; background: var(--cream); }
  body { font-family: "Montserrat", sans-serif; color: var(--ink); }

  .poster {
    position: relative;
    width: 775px;
    height: 1200px;
    overflow: hidden;
    background: linear-gradient(180deg, var(--cream) 0%, var(--cream-deep) 75%, var(--cream) 100%);
  }

  .header-band { position: absolute; left: 0; top: 0; width: 775px; height: 260px; }

  .title {
    position: absolute;
    left: 28px;
    top: 26px;
    font-weight: 800;
    font-size: 58px;
    line-height: 1.02;
    color: var(--white);
    letter-spacing: -0.5px;
  }

  .dreamcatcher {
    position: absolute;
    left: 606px;
    top: 0;
    width: 169px;
    height: 495px;
    background: linear-gradient(180deg, rgba(143,165,149,0.55), rgba(143,165,149,0.25) 60%, rgba(143,165,149,0));
    border-bottom-left-radius: 80px;
  }

  .elders-photo {
    position: absolute;
    left: 328px;
    top: 272px;
    width: 447px;
    height: 680px;
    background: radial-gradient(ellipse at 55% 35%, var(--photo-light) 0%, var(--photo-mid) 55%, rgba(207,198,180,0) 85%);
  }

  .subtitle {
    position: absolute;
    left: 28px;
    top: 252px;
    width: 420px;
    font-style: italic;
    font-weight: 700;
    font-size: 24px;
    line-height: 1.3;
    color: var(--brown);
  }
  .subtitle-rule {
    position: absolute;
    left: 28px;
    top: 348px;
    width: 393px;
    height: 3px;
    background: var(--brown);
  }

  .stat { position: absolute; left: 20px; }
  .stat-icon { position: absolute; left: 0; }
  .stat-icon.placeholder { background: var(--brown); opacity: 0.85; border-radius: 6px; }
  .stat-text { position: absolute; left: 90px; top: 0; width: 300px; }
  .stat-figure { font-weight: 800; font-size: 44px; line-height: 1; letter-spacing: -1.5px; color: var(--ink); }
  .stat-label { font-weight: 500; font-size: 16px; line-height: 1.2; color: var(--ink-soft); }

  .risk-note {
    position: absolute;
    left: 28px;
    top: 838px;
    width: 600px;
    font-style: italic;
    font-weight: 600;
    font-size: 19px;
    line-height: 1.5;
    color: var(--ink);
    letter-spacing: 0.3px;
  }

  .call-to-action {
    position: absolute;
    left: 100px;
    top: 948px;
    width: 562px;
    height: 52px;
    border-radius: 26px;
    background: var(--brown-dark);
    border: 2px solid var(--cream);
    box-shadow: 0 2px 4px rgba(0,0,0,0.25);
    color: var(--white);
    font-weight: 500;
    font-size: 16px;
    line-height: 1.2;
    text-align: center;
    padding-top: 6px;
  }
  .cta-arrow { position: absolute; top: 962px; }

  .footer-wave { position: absolute; left: 0; top: 1020px; width: 775px; height: 180px; }

  .partners {
    position: absolute;
    right: 22px;
    top: 1128px;
    display: flex;
    align-items: center;
    gap: 26px;
  }
  .partner { display: flex; align-items: center; gap: 6px; font-weight: 700; font-size: 15px; }
  .partner-dot { width: 14px; height: 14px; border-radius: 50%; }
  .partner--kestrel { color: var(--logo-red); }
  .partner--kestrel .partner-dot { background: var(--logo-red); }
  .partner--cedar { color: var(--logo-green); font-size: 12px; }
  .partner--cedar .partner-dot { background: var(--logo-green); }
</style>
</head>
<body>
<main class="poster">

  <svg class="header-band" viewBox="0 0 775 260" aria-hidden="true">
    <defs>
      <linearGradient id="bandFill" x1="0" y1="0" x2="1" y2="1">
        <stop offset="0" stop-color="#5e3d22"/>
        <stop offset="0.6" stop-color="#8a6238"/>
        <stop offset="1" stop-color="#a37848"/>
      </linearGradient>
    </defs>
    <path d="M0 0 H775 V150 C560 150 300 165 0 232 Z" fill="url(#bandFill)"/>
    <path d="M0 214 C300 150 560 138 775 140 V150 C560 150 300 165 0 232 Z" fill="#2f2319" opacity="0.8"/>
  </svg>

  <h1 class="title">Bright Trails,<br>Strong Spirits</h1>

  <div class="dreamcatcher" role="img" aria-label="Dreamcatcher with woven hoop, beads and hanging feathers"></div>

  <div class="elders-photo" role="img" aria-label="Photo of a smiling elderly couple embracing"></div>

  <p class="subtitle">The River of Life Flows<br>Through the Heart,<br>Protecting the Mind and Body</p>
  <div class="subtitle-rule"></div>

  <section class="stat" style="top:395px;">
    <div class="stat-icon placeholder" role="img" aria-label="Map of the United States" style="top:2px;width:76px;height:46px;"></div>
    <div class="stat-text" style="left:90px;">
      <div class="stat-figure">5.7 Million</div>
      <div class="stat-label">Americans have<br>Alzheimer’s disease</div>
    </div>
  </section>

  <section class="stat" style="top:498px;">
    <svg class="stat-icon" viewBox="0 0 60 60" width="60" height="60" style="top:4px;left:4px;" aria-hidden="true">
      <path d="M30 52 L9 31 C2 24 3 13 11 9 C18 5 25 8 30 15 C35 8 42 5 49 9 C57 13 58 24 51 31 Z" fill="none" stroke="#3a332d" stroke-width="2.5" stroke-linejoin="round"/>
      <path d="M6 30 H21 L25 22 L30 40 L35 26 L38 30 H54" fill="none" stroke="#6b4320" stroke-width="2.5" stroke-linejoin="round"/>
    </svg>
    <div class="stat-text" style="left:90px;">
      <div class="stat-label">Alzheimer’s is the</div>
      <div class="stat-figure" style="font-size:42px;">6th leading</div>
      <div class="stat-label">Cause of Death</div>
    </div>
  </section>

  <section class="stat" style="top:602px;">
    <div class="stat-icon placeholder" role="img" aria-label="Pictogram of a group of people with one highlighted" style="top:0;width:66px;height:80px;"></div>
    <div class="stat-text" style="left:92px;">
      <div class="stat-figure">1 in 10</div>
      <div class="stat-label">People age 65 and older<br>has Alzheimer’s</div>
    </div>
  </section>

  <section class="stat" style="top:708px;">
    <div class="stat-icon placeholder" role="img" aria-label="Illustration of a traditional feathered headdress" style="top:2px;width:60px;height:74px;"></div>
    <div class="stat-text" style="left:90px;">
      <div class="stat-figure">1 in 3</div>
      <div class="stat-label">American Indians over 65<br>develop dementia, including<br>Alzheimer’s</div>
    </div>
  </section>

  <p class="risk-note">Elders with diabetes, heart disease, or high blood pressure have a much higher risk of developing Alzheimer’s or other dementias</p>

  <svg class="cta-arrow" viewBox="0 0 60 24" width="60" height="24" style="left:38px;" aria-hidden="true">
    <path d="M4 12 H56" stroke="#6b4320" stroke-width="2" stroke-dasharray="3 3"/>
    <path d="M44 5 L56 12 L44 19" fill="none" stroke="#6b4320" stroke-width="2.5"/>
  </svg>
  <div class="call-to-action">Make an appointment with your doctor today to<br>talk about how to keep your mind and heart healthy.</div>
  <svg class="cta-arrow" viewBox="0 0 60 24" width="60" height="24" style="left:668px;" aria-hidden="true">
    <path d="M4 12 H56" stroke="#6b4320" stroke-width="2" stroke-dasharray="3 3"/>
    <path d="M16 5 L4 12 L16 19" fill="none" stroke="#6b4320" stroke-width="2.5"/>
  </svg>

  <svg class="footer-wave" viewBox="0 0 775 180" aria-hidden="true">
    <path d="M0 40 C200 10 420 110 775 40" fill="none" stroke="#c9a97c" stroke-width="3" opacity="0.7"/>
    <path d="M0 55 C200 25 420 125 775 55" fill="none" stroke="#c9a97c" stroke-width="3" opacity="0.6"/>
    <path d="M0 70 C200 40 420 140 775 70" fill="none" stroke="#c9a97c" stroke-width="3" opacity="0.5"/>
    <path d="M0 90 C220 50 440 150 775 85 V180 H0 Z" fill="#ffffff"/>
  </svg>

  <div class="partners">
    <div class="partner partner--kestrel"><span class="partner-dot"></span>Kestrel Health</div>
    <div class="partner partner--cedar"><span class="partner-dot"></span>Cedar Circle Elders Network</div>
  </div>

</main>
</body>
</html>
```